The most modern business card ever !!!

Our company call “Vendalo”. Vendalo is a technology company specialized in cruises solutions. Out main product is a platform to reserve cruises. This is a revolutionary platform that make easier to travel agencies and final users to reserve cruises across dozen companies like tibba, wernu, hpv, dgb, etc..We are a “start up”, with a young team of developers and we want to transmit it.. For it, we want something different, a modern business card that represent cruises and technology.. When someone receive this card, this person should say: wowww this is different… this is modern… this is a cruise related company..
- diferent, modern
- traditions business card

```html
<!DOCTYPE html>
<html lang="en">
<head>
<meta charset="utf-8">
<title>Vendalo Business Card</title>
<link href="https://fonts.googleapis.com/css2?family=Lato:wght@400;700&display=swap" rel="stylesheet">
<style>
  :root {
    --backdrop: #2a2a2b;
    --card: #1c1d1f;
    --card-back-top: #202123;
    --card-back-bottom: #17181a;
    --white: #ffffff;
    --accent: #29a8e0;
    --muted: #c9c9c9;
    --rule: #6a6a6a;
    --silver: #d6d6d6;
  }
  * { margin: 0; padding: 0; box-sizing: border-box; }
  html, body {
    width: 1200px; height: 1108px; overflow: hidden;
    background: var(--backdrop);
    font-family: "Lato", Arial, sans-serif;
  }
  .canvas {
    position: relative; width: 1200px; height: 1108px;
    display: flex; justify-content: center; align-items: center; gap: 80px;
  }
  .card {
    position: relative; width: 400px; height: 640px;
    border-radius: 26px; background: var(--card);
    box-shadow: 0 18px 40px rgba(0,0,0,.45);
    overflow: hidden;
  }
  .card-front { padding: 120px 48px 0; color: var(--muted); }
  .brand-name {
    font-size: 76px; font-weight: 700; color: var(--white);
    letter-spacing: 1px; line-height: 1; text-align: center;
  }
  .person { margin-top: 110px; text-align: center; }
  .person-name {
    font-size: 25px; font-weight: 400; color: var(--accent);
    letter-spacing: .5px; text-transform: uppercase;
  }
  .person-role { font-size: 19px; color: var(--muted); margin-top: 2px; }
  .icon-rule {
    display: flex; align-items: center; gap: 10px; margin: 16px 0 10px;
  }
  .icon-rule .rule { flex: 1; height: 1px; background: var(--rule); }
  .icon-rule .icons { display: flex; gap: 5px; }
  .icon-rule svg { width: 22px; height: 22px; display: block; }
  .contact { text-align: center; font-size: 20px; line-height: 1.3; color: var(--muted); }
  .divider { height: 1px; background: var(--rule); margin: 12px 0; }
  .card-back {
    background: linear-gradient(180deg, var(--card-back-top), var(--card-back-bottom));
  }
  .texture-field {
    position: absolute; left: 0; top: 0; width: 100%; height: 440px;
    background: linear-gradient(180deg, #2a2b2d 0%, #222325 60%, rgba(23,24,26,0) 100%);
  }
  .back-brand {
    position: absolute; left: 0; right: 0; bottom: 90px;
    text-align: center; font-size: 76px; font-weight: 700;
    color: var(--silver); letter-spacing: 1px; line-height: 1;
  }
</style>
</head>
<body>
<main class="canvas">
  <section class="card card-front">
    <div class="brand-name">Vendalo</div>
    <div class="person">
      <div class="person-name">Marcus Reyel</div>
      <div class="person-role">Managing Director</div>
    </div>
    <div class="icon-rule">
      <span class="rule"></span>
      <span class="icons">
        <svg viewBox="0 0 22 22" aria-label="phone"><circle cx="11" cy="11" r="11" fill="var(--accent)"/><path d="M8 6.5c.6-.4 1.2-.2 1.5.4l.6 1.3c.2.5 0 1-.4 1.3l-.5.4c.5 1.1 1.3 2 2.4 2.5l.4-.5c.3-.4.9-.6 1.3-.4l1.3.6c.6.3.8.9.4 1.5-.6 1-1.7 1.4-2.8.9-2.2-1-4-2.8-5-5-.4-1 0-2.1 1-2.8z" fill="var(--card)"/></svg>
        <svg viewBox="0 0 22 22" aria-label="email"><circle cx="11" cy="11" r="11" fill="var(--accent)"/><rect x="5.5" y="7" width="11" height="8" rx="1" fill="var(--card)"/><path d="M6 7.8l5 3.8 5-3.8" stroke="var(--accent)" stroke-width="1" fill="none"/></svg>
        <svg viewBox="0 0 22 22" aria-label="location"><circle cx="11" cy="11" r="11" fill="var(--accent)"/><path d="M11 5a4 4 0 0 0-4 4c0 3 4 8 4 8s4-5 4-8a4 4 0 0 0-4-4z" fill="var(--card)"/><circle cx="11" cy="9" r="1.5" fill="var(--accent)"/></svg>
      </span>
      <span class="rule"></span>
    </div>
    <div class="contact">
      <div>444 555 2719</div>
      <div>hello@vendalomail.com</div>
      <div>www.vendalosite.com</div>
    </div>
    <div class="divider"></div>
    <div class="contact">
      <div>738, Harbor Lane West,</div>
      <div>Porto Nuvia, 60318</div>
    </div>
  </section>

  <section class="card card-back">
    <div class="texture-field" role="img" aria-label="Subtle repeating brand-initial pattern in dark grey tones"></div>
    <div class="back-brand">Vendalo</div>
  </section>
</main>
</body>
</html>
```